Executive Business Card for Healthcare Company [Need Today]

I need a business card design for a healthcare company. The only branding the company has thus far is a logo. The cards will be utilized by company executives. The design I envision will be vibrant and appealing but with a corporate feel. They shouldn't be too casual or playful. I would like to complete this project TODAY if possible.

Target Market(s)

Healthcare vendors, other executives in healthcare and pharmaceuticals

Industry/Entity Type

Pharmaceutical

Contact Information for Business Card

See attachment

Font styles to use
Serif
Sans Serif

Colors

Designer to choose colors to be used in the design.

```html
<!DOCTYPE html>
<html lang="en">
<head>
<meta charset="UTF-8">
<title>Calden Therapeutics – Executive Business Card</title>
<link rel="stylesheet" href="https://fonts.googleapis.com/css2?family=Montserrat:wght@300;400;500;600&display=swap">
<style>
  :root {
    --backdrop: #3b3b3d;
    --card-black: #1b1b1d;
    --card-black-soft: #232326;
    --teal: #2fc1b4;
    --teal-deep: #1fa89c;
    --silver: #8e8f93;
    --silver-light: #b9babd;
    --white: #f4f5f5;
  }
  * { box-sizing: border-box; margin: 0; padding: 0; }
  html, body { width: 800px; height: 1200px; overflow: hidden; }
  body {
    background: var(--backdrop);
    font-family: "Montserrat", sans-serif;
    display: flex;
    flex-direction: column;
    align-items: center;
    justify-content: center;
    gap: 110px;
  }
  .card {
    position: relative;
    width: 640px;
    height: 366px;
    background: var(--card-black);
    border-radius: 4px;
    overflow: hidden;
    box-shadow: 0 18px 40px rgba(0,0,0,0.35);
  }

  /* Front side */
  .card-front .brand {
    position: absolute;
    left: 0; right: 0; top: 128px;
    display: flex;
    align-items: center;
    justify-content: center;
    gap: 18px;
  }
  .brand-dot {
    width: 54px; height: 54px;
    border-radius: 50%;
    border: 2px solid var(--silver);
  }
  .card-front .brand-name {
    font-weight: 400;
    font-size: 38px;
    letter-spacing: 1px;
    color: var(--silver);
  }
  .card-front .website {
    position: absolute;
    left: 0; right: 0; bottom: 70px;
    text-align: center;
    font-size: 13px;
    letter-spacing: 2px;
    color: var(--white);
  }

  /* Back side */
  .card-back .brand {
    position: absolute;
    left: 36px; top: 36px;
    display: flex;
    align-items: center;
    gap: 12px;
  }
  .card-back .brand-dot {
    width: 44px; height: 44px;
    border-color: var(--teal);
  }
  .card-back .brand-name {
    font-weight: 400;
    font-size: 28px;
    color: var(--teal);
    letter-spacing: 0.5px;
  }
  .person {
    position: absolute;
    left: 36px; top: 114px;
  }
  .person-name {
    font-size: 22px;
    font-weight: 500;
    color: var(--teal);
  }
  .person-title {
    margin-top: 3px;
    font-size: 10px;
    font-weight: 400;
    color: var(--silver-light);
    letter-spacing: 0.3px;
  }
  .wave {
    position: absolute;
    left: 0; bottom: 0;
    width: 640px; height: 230px;
  }
  .contact {
    position: absolute;
    right: 30px; top: 190px;
    list-style: none;
    text-align: right;
    font-size: 11px;
    color: var(--white);
    line-height: 19px;
  }
  .contact li {
    display: flex;
    align-items: center;
    justify-content: flex-end;
    gap: 7px;
  }
  .contact svg { width: 10px; height: 10px; }
  .address {
    position: absolute;
    right: 30px; bottom: 18px;
    font-size: 11px;
    color: var(--white);
    letter-spacing: 0.3px;
  }
</style>
</head>
<body>

  <section class="card card-front">
    <div class="brand">
      <span class="brand-dot"></span>
      <span class="brand-name">Calden Therapeutics</span>
    </div>
    <p class="website">www.caldenrx.com</p>
  </section>

  <section class="card card-back">
    <div class="brand">
      <span class="brand-dot"></span>
      <span class="brand-name">Calden Therapeutics</span>
    </div>

    <div class="person">
      <p class="person-name">Martin Hale</p>
      <p class="person-title">Senior Director of Marketing</p>
    </div>

    <svg class="wave" viewBox="0 0 640 230" preserveAspectRatio="none" aria-hidden="true">
      <path d="M0 120 C 150 60, 300 40, 420 70 C 520 95, 590 90, 640 60 L640 230 L0 230 Z" fill="var(--silver)"/>
      <path d="M0 140 C 150 80, 300 62, 420 92 C 520 116, 590 112, 640 84 L640 230 L0 230 Z" fill="var(--card-black-soft)"/>
      <path d="M0 162 C 160 100, 310 90, 430 118 C 530 140, 595 132, 640 108 L640 230 L0 230 Z" fill="var(--teal)"/>
      <path d="M0 230 L0 200 C 200 150, 380 190, 640 160 L640 230 Z" fill="var(--teal-deep)" opacity="0.5"/>
    </svg>

    <ul class="contact">
      <li>555.210.0142
        <svg viewBox="0 0 10 10"><path d="M2 1 L4 1 L4.6 3 L3.5 3.8 C4 5 5 6 6.2 6.5 L7 5.4 L9 6 L9 8 C5 8.5 1.5 5 2 1 Z" fill="currentColor"/></svg>
      </li>
      <li>555.210.0187
        <svg viewBox="0 0 10 10"><rect x="2.5" y="0.5" width="5" height="9" rx="1" fill="none" stroke="currentColor"/></svg>
      </li>
      <li>mhale@caldenrx.com
        <svg viewBox="0 0 10 10"><rect x="0.5" y="2" width="9" height="6" fill="none" stroke="currentColor"/><path d="M0.5 2 L5 5.5 L9.5 2" fill="none" stroke="currentColor"/></svg>
      </li>
      <li>www.caldenrx.com
        <svg viewBox="0 0 10 10"><circle cx="5" cy="5" r="4.2" fill="none" stroke="currentColor"/><path d="M0.8 5 H9.2 M5 0.8 C3 3, 3 7, 5 9.2 M5 0.8 C7 3, 7 7, 5 9.2" fill="none" stroke="currentColor" stroke-width="0.7"/></svg>
      </li>
    </ul>

    <p class="address">118 W Lanier Street Marlow, OK 73055</p>
  </section>

</body>
</html>
```